Vantrel Activated Carbon (coal-based)

The packaging for granular activated carbon must have a simple industrial concept but looks classy. Industrial look, bold and credible, also eye catching. Weight: 25 kg

Target Market(s)

Industrial

Industry/Entity Type

Water Treatment Industry

Requirements
Must have
• Weight : 25 kg, must have "coal-based", warning symbol in packaging
Nice to have
• There is a picture of granular activated carbon (coal-based) on the package

```html
<!DOCTYPE html>
<html lang="en">
<head>
<meta charset="utf-8">
<title>Vantrel Activated Carbon – 25 kg bag dieline</title>
<link href="https://fonts.googleapis.com/css2?family=Montserrat:wght@400;600;700;800;900&family=Saira+Semi+Condensed:wght@300;400&family=Noto+Sans+Arabic:wght@500&display=swap" rel="stylesheet">
<style>
  :root{
    --stage:#4a7db6;
    --ink:#000000;
    --band:#0c4e93;
    --brand:#1763ae;
    --white:#ffffff;
    --grey:#8a8a8a;
    --fold:#1e1e1e;
  }
  html,body{margin:0;padding:0;width:708px;height:1200px;overflow:hidden;background:var(--stage);}
  .dieline{position:absolute;left:22px;top:328px;width:664px;height:543px;display:block;}
  .panel{fill:var(--ink);}
  .gusset-band{fill:var(--band);}
  .fold-line{stroke:var(--fold);stroke-width:1;}
  .brand-name{font-family:"Montserrat",sans-serif;font-weight:900;fill:var(--brand);letter-spacing:0.5px;}
  .brand-name--dark{fill:var(--ink);}
  .coal-based{font-family:"Montserrat",sans-serif;font-weight:600;fill:var(--white);}
  .coal-based--dark{fill:var(--ink);}
  .premium-tag{fill:var(--brand);}
  .premium-tag--dark{fill:var(--ink);}
  .premium-text{font-family:"Montserrat",sans-serif;font-weight:600;fill:var(--white);}
  .premium-text--blue{fill:#9fc3ea;}
  .product-name{font-family:"Montserrat",sans-serif;font-weight:800;fill:var(--white);}
  .product-name--dark{fill:var(--ink);}
  .rule{stroke:var(--grey);stroke-width:1;}
  .rule--white{stroke:var(--white);stroke-width:2;}
  .languages{font-family:"Saira Semi Condensed","Noto Sans Arabic",sans-serif;font-weight:300;fill:var(--white);}
  .warning-title{font-family:"Montserrat",sans-serif;font-weight:700;fill:var(--white);}
  .warning-body{font-family:"Montserrat",sans-serif;font-weight:400;fill:var(--white);}
  .hazard-note{font-family:"Montserrat",sans-serif;font-weight:400;fill:var(--white);}
  .icon-box{fill:none;stroke:var(--white);stroke-width:1.6;}
  .icon-mark{fill:none;stroke:var(--white);stroke-width:1.4;}
  .batch-label{font-family:"Montserrat",sans-serif;font-weight:700;fill:var(--white);}
  .batch-field{fill:var(--white);}
  .grade-badge{fill:none;stroke:var(--white);stroke-width:2;}
  .grade-label{font-family:"Montserrat",sans-serif;font-weight:800;fill:var(--white);}
  .claims{font-family:"Montserrat",sans-serif;font-weight:400;fill:var(--white);}
  .weight-hex{fill:var(--band);}
  .weight-text{font-family:"Montserrat",sans-serif;font-weight:600;fill:var(--white);}
</style>
</head>
<body>
<svg class="dieline" viewBox="0 0 1106 904" xmlns="http://www.w3.org/2000/svg" aria-label="Flat dieline of the Vantrel 25 kg activated carbon bag">
  <defs>
    <linearGradient id="hexBlue" x1="0" y1="0" x2="1" y2="1">
      <stop offset="0" stop-color="#0c4e93"/>
      <stop offset="0.6" stop-color="#0a3e76"/>
      <stop offset="1" stop-color="#000000"/>
    </linearGradient>
    <linearGradient id="hexGrey" x1="0" y1="0" x2="1" y2="1">
      <stop offset="0" stop-color="#3a3a3a"/>
      <stop offset="1" stop-color="#555555"/>
    </linearGradient>
  </defs>

  <!-- panels -->
  <rect class="panel" x="0" y="0" width="1106" height="904"/>
  <rect class="gusset-band" x="401" y="152" width="152" height="600"/>
  <rect class="gusset-band" x="953" y="152" width="153" height="600"/>
  <g class="fold-lines">
    <line class="fold-line" x1="0" y1="152" x2="1106" y2="152"/>
    <line class="fold-line" x1="0" y1="752" x2="1106" y2="752"/>
    <line class="fold-line" x1="401" y1="0" x2="401" y2="904"/>
    <line class="fold-line" x1="553" y1="0" x2="553" y2="904"/>
    <line class="fold-line" x1="953" y1="0" x2="953" y2="904"/>
  </g>

  <!-- back panel -->
  <g class="back-panel">
    <rect x="178" y="188" width="352" height="202" rx="24" fill="url(#hexBlue)" opacity="0.85" role="img" aria-label="Cluster of blue hexagon shapes suggesting carbon granules"/>
    <text class="brand-name" x="201" y="423" font-size="40" text-anchor="middle">VANTREL</text>
    <text class="coal-based" x="303" y="445" font-size="9" text-anchor="end">COAL-BASED</text>
    <rect class="premium-tag" x="102" y="447" width="66" height="18" rx="2"/>
    <text class="premium-text" x="135" y="460" font-size="11" text-anchor="middle">PREMIUM</text>
    <text class="product-name" x="303" y="460" font-size="12" text-anchor="end">ACTIVATED CARBON</text>

    <line class="rule--white" x1="79" y1="496" x2="209" y2="496"/>
    <g class="warning-symbol">
      <path d="M87 506 L96 521 L78 521 Z" fill="none" stroke="#e02020" stroke-width="2"/>
      <text x="87" y="519" font-size="9" font-family="Montserrat,sans-serif" font-weight="800" fill="#ffffff" text-anchor="middle">!</text>
    </g>
    <text class="warning-title" x="99" y="520" font-size="10">WARNING / CAUTION</text>
    <rect x="225" y="505" width="12" height="12" transform="rotate(45 231 511)" fill="#ffffff" stroke="#e02020" stroke-width="2"/>
    <rect x="248" y="505" width="12" height="12" transform="rotate(45 254 511)" fill="#ffffff" stroke="#e02020" stroke-width="2"/>
    <text class="hazard-note" x="272" y="507" font-size="5.5">Harmful if inhaled.</text>
    <text class="hazard-note" x="272" y="514" font-size="5.5">Eye irritant</text>

    <g class="warning-body" font-size="10.5">
      <text x="79" y="534" textLength="243" lengthAdjust="spacing">Activated carbon affects the respiratory and</text>
      <text x="79" y="548" textLength="243" lengthAdjust="spacing">cardiovascular system. Wet activated carbon can</text>
      <text x="79" y="562" textLength="243" lengthAdjust="spacing">deplete oxygen from the air creating dangerously</text>
      <text x="79" y="576" textLength="243" lengthAdjust="spacing">low levels of oxygen in confined spaces. Please pay</text>
      <text x="79" y="590">attention to working in confined spaces.</text>
    </g>

    <g class="handling-icons">
      <rect class="icon-box" x="79" y="618" width="26" height="26" rx="3"/>
      <path class="icon-mark" d="M86 628 h12 v9 h-12 z M92 624 v4"/>
      <rect class="icon-box" x="119" y="618" width="26" height="26" rx="3"/>
      <path class="icon-mark" d="M124 630 q8 -9 16 0 z M132 630 v8 q0 2 -2 2"/>
      <rect class="icon-box" x="159" y="618" width="26" height="26" rx="3"/>
      <circle class="icon-mark" cx="172" cy="631" r="4"/>
      <path class="icon-mark" d="M172 622 v3 M172 637 v3 M163 631 h3 M178 631 h3"/>
      <rect class="icon-box" x="199" y="618" width="26" height="26" rx="3"/>
      <path class="icon-mark" d="M212 622 v18 M208 626 h8 M208 634 h8"/>
      <rect class="icon-box" x="239" y="618" width="26" height="26" rx="3"/>
      <path class="icon-mark" d="M252 623 l6 10 h-12 z"/>
    </g>

    <text class="batch-label" x="79" y="672" font-size="6.5">BATCH NUMBER</text>
    <rect class="batch-field" x="79" y="680" width="104" height="23" rx="2"/>
  </g>

  <!-- left gusset -->
  <g class="gusset gusset--left">
    <text class="brand-name brand-name--dark" transform="translate(471 713) rotate(-90)" font-size="46">VANTREL</text>
    <text class="coal-based coal-based--dark" transform="translate(496 608) rotate(-90)" font-size="9" text-anchor="end">COAL-BASED</text>
    <rect class="premium-tag premium-tag--dark" x="498" y="608" width="18" height="76" rx="2"/>
    <text class="premium-text" transform="translate(511 678) rotate(-90)" font-size="11">PREMIUM</text>
    <text class="product-name product-name--dark" transform="translate(512 603) rotate(-90)" font-size="13">ACTIVATED CARBON</text>
  </g>

  <!-- front panel -->
  <g class="front-panel">
    <rect x="596" y="190" width="177" height="104" rx="18" fill="url(#hexGrey)" role="img" aria-label="Small cluster of grey hexagon shapes"/>
    <text class="brand-name" x="753" y="373" font-size="53" text-anchor="middle">VANTREL</text>
    <text class="coal-based" x="886" y="393" font-size="11" text-anchor="end">COAL-BASED</text>
    <rect class="premium-tag" x="621" y="398" width="85" height="23" rx="3"/>
    <text class="premium-text" x="663" y="415" font-size="14" text-anchor="middle">PREMIUM</text>
    <text class="product-name" x="886" y="415" font-size="16" text-anchor="end">ACTIVATED CARBON</text>
    <line class="rule" x1="621" y1="433" x2="886" y2="433"/>
    <text class="languages" x="753" y="457" font-size="13" text-anchor="middle">活性炭  I  Активированный уголь  I  كربون مفعل</text>
    <text class="languages" x="753" y="479" font-size="13" text-anchor="middle">Charbon actif  I  Geactiveerde koolstof</text>

    <rect x="748" y="512" width="356" height="200" rx="26" fill="url(#hexBlue)" opacity="0.85" role="img" aria-label="Cluster of blue and black hexagon shapes suggesting carbon granules"/>
    <polygon class="weight-hex" points="878,640 911,659 911,697 878,716 845,697 845,659"/>
    <text class="weight-text" x="878" y="673" font-size="10.5" text-anchor="middle">Weight</text>
    <text class="weight-text" x="878" y="687" font-size="10.5" text-anchor="middle">25Kg</text>

    <circle class="grade-badge" cx="616" cy="628" r="19"/>
    <text class="grade-label" x="594" y="660" font-size="7.5">HIGH-GRADE</text>
    <g class="claims" font-size="7.2">
      <text x="594" y="683">ORDERS AND IMPURITIES*</text>
      <text x="594" y="693">FOR SPARKLING CLEAN WATER</text>
      <text x="594" y="703">IDEAL FOR ALL AQUARIUM FILTERS</text>
    </g>
  </g>

  <!-- right gusset -->
  <g class="gusset gusset--right">
    <text class="brand-name brand-name--dark" transform="translate(1023 480) rotate(-90)" font-size="44">VANTREL</text>
    <text class="coal-based coal-based--dark" transform="translate(1048 285) rotate(-90)" font-size="9" text-anchor="end">COAL-BASED</text>
    <rect class="premium-tag premium-tag--dark" x="1049" y="373" width="18" height="76" rx="2"/>
    <text class="premium-text" transform="translate(1062 443) rotate(-90)" font-size="11">PREMIUM</text>
    <text class="product-name product-name--dark" transform="translate(1063 368) rotate(-90)" font-size="13">ACTIVATED CARBON</text>
  </g>
</svg>
</body>
</html>
```